Barrister at Law needs Business Card Design

Need a business card design for Barrister at Law. Double sided. Simple Neil Thorsby and Barrister at Law on one side with contact details on the other side. I would like a professional design using Black or Platinum. Details on reverse side would include qualifications - Bcom-Llb and Acc Spec Commercial Litigation. I have attached the logo. Contact details would include address/ Po Box/ Phone/Fax/Mobile/email. I would like to use raised print or spot gloss.

```html
<!DOCTYPE html>
<html lang="en">
<head>
<meta charset="utf-8">
<title>Neil Thorsby — Barrister-at-Law Business Card</title>
<link href="https://fonts.googleapis.com/css2?family=Cinzel:wght@400;500&family=Open+Sans:wght@400;600&display=swap" rel="stylesheet">
<style>
  :root {
    --page-bg: #2b2725;
    --card-black: #141414;
    --card-edge: #1f1f1f;
    --accent-blue: #1f73c4;
    --accent-blue-light: #3b8fdc;
    --platinum: #a9a9a9;
    --text-light: #e6e6e6;
    --divider: #5a5a5a;
  }
  html, body {
    margin: 0;
    padding: 0;
    width: 1200px;
    height: 814px;
    overflow: hidden;
    background: var(--page-bg);
  }
  .canvas {
    position: relative;
    width: 1200px;
    height: 814px;
  }
  .card {
    position: absolute;
    top: 257px;
    width: 520px;
    height: 300px;
    background: var(--card-black);
    border: 1px solid var(--card-edge);
    box-sizing: border-box;
    overflow: hidden;
  }
  .card--front { left: 60px; }
  .card--back  { left: 620px; }

  /* Front */
  .front-name {
    position: absolute;
    left: 70px;
    top: 96px;
    margin: 0;
    font-family: "Cinzel", serif;
    font-weight: 500;
    font-size: 34px;
    letter-spacing: 1px;
    color: var(--accent-blue);
    text-transform: uppercase;
  }
  .front-title {
    position: absolute;
    left: 70px;
    top: 144px;
    margin: 0;
    font-family: "Cinzel", serif;
    font-weight: 400;
    font-size: 24px;
    letter-spacing: 1px;
    color: var(--platinum);
    text-transform: uppercase;
  }

  /* Back */
  .brand {
    position: absolute;
    left: 36px;
    top: 112px;
    width: 140px;
    display: flex;
    align-items: center;
    gap: 8px;
  }
  .brand-square {
    width: 12px;
    height: 12px;
    background: var(--accent-blue);
    flex: none;
  }
  .brand-name {
    font-family: "Open Sans", sans-serif;
    font-weight: 600;
    font-size: 19px;
    color: #ffffff;
    white-space: nowrap;
  }
  .divider {
    position: absolute;
    left: 196px;
    top: 52px;
    width: 1px;
    height: 150px;
    background: var(--divider);
  }
  .contact {
    position: absolute;
    left: 222px;
    top: 58px;
    font-family: "Open Sans", sans-serif;
    font-size: 13.5px;
    line-height: 20px;
    color: var(--text-light);
  }
  .contact-address { margin: 0 0 4px 28px; }
  .contact-list {
    list-style: none;
    margin: 0;
    padding: 0;
  }
  .contact-list li {
    display: flex;
    align-items: center;
    gap: 10px;
    height: 21px;
  }
  .contact-list li.contact-email { margin-top: 12px; }
  .contact-icon {
    width: 16px;
    height: 16px;
    flex: none;
    fill: var(--accent-blue-light);
  }
  .contact-list li.contact-email .contact-icon { visibility: hidden; }
  .contact-list li.contact-email { padding-left: 0; }
  .bands {
    position: absolute;
    left: 0;
    bottom: 0;
    width: 520px;
    height: 300px;
  }
  .website {
    position: absolute;
    right: 36px;
    bottom: 10px;
    font-family: "Open Sans", sans-serif;
    font-size: 15px;
    letter-spacing: 3px;
    color: #ffffff;
  }
</style>
</head>
<body>
<div class="canvas">

  <section class="card card--front" aria-label="Card front">
    <h1 class="front-name">Neil Thorsby</h1>
    <p class="front-title">Barrister-at-Law</p>
  </section>

  <section class="card card--back" aria-label="Card back">
    <svg class="bands" viewBox="0 0 520 300" aria-hidden="true">
      <polygon points="0,248 272,248 259,262 0,262" fill="#9a9a9a"/>
      <polygon points="0,262 259,262 276,244 520,244 520,300 290,300 272,274 0,274" fill="var(--accent-blue)"/>
    </svg>

    <div class="brand">
      <span class="brand-square"></span>
      <span class="brand-name">Thorsby Law</span>
    </div>

    <div class="divider"></div>

    <div class="contact">
      <p class="contact-address">42 Halden Court<br>Westbury, Carrow 20418</p>
      <ul class="contact-list">
        <li>
          <svg class="contact-icon" viewBox="0 0 16 16" aria-hidden="true"><path d="M4 1.5l2 3-1.3 1.5c.8 1.9 2.4 3.5 4.3 4.3L10.5 9l3 2-1 2.5C7 13 3 9 2.5 3.5z"/></svg>
          <span>604 215 7390</span>
        </li>
        <li>
          <svg class="contact-icon" viewBox="0 0 16 16" aria-hidden="true"><path d="M4.5 1h7a1 1 0 0 1 1 1v12a1 1 0 0 1-1 1h-7a1 1 0 0 1-1-1V2a1 1 0 0 1 1-1zm.5 2v9h6V3zm3 10a.8.8 0 1 0 0 1.6.8.8 0 0 0 0-1.6z"/></svg>
          <span>731 902 4486</span>
        </li>
        <li>
          <svg class="contact-icon" viewBox="0 0 16 16" aria-hidden="true"><path d="M4 1h6l2 2v3H4zM2 7h12a1 1 0 0 1 1 1v6H1V8a1 1 0 0 1 1-1zm2 2v1.5h2V9zm4 0v1.5h4V9z"/></svg>
          <span>559 318 6027</span>
        </li>
        <li>
          <svg class="contact-icon" viewBox="0 0 16 16" aria-hidden="true" style="visibility:visible"><path d="M1 3h14v10H1zm1.5 1.5v.4L8 8.6l5.5-3.7v-.4z"/></svg>
          <span>neil@thorsbylaw.com</span>
        </li>
      </ul>
    </div>

    <div class="website">www.thorsbylaw.com</div>
  </section>

</div>
</body>
</html>
```